Upscale business cards needed for Board of Directors

We need professional business cards created for members of our family business Board of Directors. We would like these relatively simple and straightforward, but also with a unique element to set them apart. Probably stick with neutral and simple colors - white, grey etc. We need space for the traditional elements, including name, title, address, email/phone number. And we will be creating several from this template so it needs to be template that is easy to switch information in and out of.
Business
See description

```html
<!DOCTYPE html>
<html lang="en">
<head>
<meta charset="utf-8">
<title>Harbourline Holdings – Business Cards</title>
<link href="https://fonts.googleapis.com/css2?family=Rajdhani:wght@700&family=Arimo:wght@400&display=swap" rel="stylesheet">
<style>
  :root {
    --stage: #e9e6e1;
    --card: #ffffff;
    --ink: #2f2d2b;
    --text: #1c1c1c;
    --gold: #cfc3a1;
    --black: #0c0c0c;
    --rule: #c9c2b0;
    --shadow: rgba(40, 30, 20, 0.28);
  }
  * { margin: 0; padding: 0; box-sizing: border-box; }
  html, body { width: 1200px; height: 902px; overflow: hidden; }
  body { background: var(--stage); position: relative; font-family: "Arimo", Arial, sans-serif; }

  .card {
    position: absolute;
    width: 640px;
    height: 366px;
    background: var(--card);
    box-shadow: 0 14px 30px var(--shadow);
    overflow: hidden;
  }
  .card--front { left: 280px; top: 70px; }
  .card--back  { left: 280px; top: 466px; }

  .wordmark {
    font-family: "Rajdhani", "Arial Narrow", sans-serif;
    font-weight: 700;
    color: var(--ink);
    text-transform: uppercase;
    text-align: center;
    line-height: 1;
  }
  .wordmark__line { display: block; letter-spacing: 2px; }
  .card--front .wordmark {
    position: absolute; left: 0; right: 0; top: 132px;
    font-size: 50px;
  }
  .card--front .wordmark__line + .wordmark__line { font-size: 34px; letter-spacing: 10px; margin-top: 8px; }

  .card--back .wordmark {
    position: absolute; left: 30px; width: 300px; top: 128px;
    font-size: 38px;
  }
  .card--back .wordmark__line + .wordmark__line { font-size: 26px; letter-spacing: 8px; margin-top: 6px; }

  .divider {
    position: absolute; left: 340px; top: 34px;
    width: 1px; height: 250px; background: var(--rule);
  }

  .contact { position: absolute; left: 366px; top: 44px; color: var(--text); }
  .contact__name { font-size: 24px; line-height: 1.1; }
  .contact__title { font-size: 17px; margin-top: 2px; }
  .contact__list { list-style: none; margin-top: 50px; }
  .contact__item { display: flex; align-items: center; font-size: 19px; height: 30px; margin-bottom: 6px; }
  .contact__icon {
    width: 18px; height: 18px; background: var(--gold);
    margin-right: 12px; flex: none; display: flex; align-items: center; justify-content: center;
  }
  .contact__icon svg { width: 12px; height: 12px; fill: var(--ink); }

  .band-gold { position: absolute; left: 0; right: 0; bottom: 44px; height: 11px; background: var(--gold); }
  .band-black { position: absolute; left: 0; right: 0; bottom: 0; height: 44px; background: var(--black); }
</style>
</head>
<body>

  <section class="card card--front" aria-label="Card front">
    <div class="wordmark">
      <span class="wordmark__line">Harbourline</span>
      <span class="wordmark__line">Holdings</span>
    </div>
  </section>

  <section class="card card--back" aria-label="Card back">
    <div class="wordmark">
      <span class="wordmark__line">Harbourline</span>
      <span class="wordmark__line">Holdings</span>
    </div>

    <div class="divider"></div>

    <div class="contact">
      <p class="contact__name">Tom Reeve</p>
      <p class="contact__title">Managing Director</p>
      <ul class="contact__list">
        <li class="contact__item">
          <span class="contact__icon"><svg viewBox="0 0 12 12"><path d="M2.4 0.8l2 2-1 1.3c.7 1.5 1.9 2.8 3.5 3.5l1.3-1 2 2-1.3 1.6C5 10 2 7 .8 2.1z"/></svg></span>
          021-555-0143
        </li>
        <li class="contact__item">
          <span class="contact__icon"><svg viewBox="0 0 12 12"><path d="M1 3h10v6H1z M1.5 3.5L6 7l4.5-3.5" fill="none" stroke="#2f2d2b" stroke-width="1.2"/></svg></span>
          harbourlinegroup@mail.com
        </li>
        <li class="contact__item">
          <span class="contact__icon"><svg viewBox="0 0 12 12"><path d="M6 0.8a3.7 3.7 0 0 0-3.7 3.7C2.3 7.3 6 11.2 6 11.2s3.7-3.9 3.7-6.7A3.7 3.7 0 0 0 6 .8zm0 5.2a1.5 1.5 0 1 1 0-3 1.5 1.5 0 0 1 0 3z"/></svg></span>
          408 N Calder Rd
        </li>
      </ul>
    </div>

    <div class="band-gold"></div>
    <div class="band-black"></div>
  </section>

</body>
</html>
```